Vantro cards

I am in the auto motive, transportation business I would like a business card that is Something cool, modern edgy, having to do with car culture. I offer towing service for high and exotic cars. I also provide towing for collisions and car accidents. I offer open and enclosed transport nationwide.

Target Market(s)

Car culture people high end auto collectors

Industry/Entity Type

Towing car carrier

Contact Information for Business Card

My company colors black yellow and silver

Font styles to use
Serif

```html
<!DOCTYPE html>
<html lang="en">
<head>
<meta charset="utf-8">
<title>Vantro Transportation – Business Cards</title>
<link rel="stylesheet" href="https://fonts.googleapis.com/css2?family=Montserrat:wght@400;600;700&display=swap">
<style>
  :root {
    --black: #000000;
    --white: #ffffff;
    --yellow: #f9dd4b;
    --ink: #111111;
    --muted: #e6e6e6;
    --stage: #e4e1db;
    --radius: 36px;
  }
  * { box-sizing: border-box; margin: 0; padding: 0; }
  html, body { width: 900px; height: 1200px; overflow: hidden; }
  body {
    position: relative;
    background: var(--stage);
    font-family: "Montserrat", Arial, sans-serif;
  }
  .card {
    position: absolute;
    left: 80px;
    width: 742px;
    height: 442px;
    border-radius: var(--radius);
    overflow: hidden;
    background: var(--white);
  }
  .card--front { top: 131px; }
  .card--back { top: 638px; }

  /* Front */
  .front__brand {
    position: absolute;
    left: 0; top: 0;
    width: 371px; height: 100%;
    display: flex; align-items: center; justify-content: center;
  }
  .front__panel {
    position: absolute;
    left: 371px; top: 0;
    width: 371px; height: 100%;
    background: var(--black);
  }
  .front__accent {
    position: absolute;
    left: 371px; top: 187px;
    width: 6px; height: 72px;
    background: var(--yellow);
    border-radius: 0 3px 3px 0;
  }
  .brand-name {
    font-weight: 700;
    color: var(--ink);
    text-align: center;
    text-transform: uppercase;
    letter-spacing: 1px;
    line-height: 1.2;
  }
  .brand-name--front { font-size: 30px; }
  .brand-name--back { font-size: 30px; }

  .contact {
    position: absolute;
    left: 407px; top: 106px;
    color: var(--white);
  }
  .contact__name {
    font-size: 26px;
    font-weight: 600;
    color: var(--yellow);
    line-height: 1.2;
  }
  .contact__role {
    font-size: 16px;
    font-weight: 400;
    margin-top: 2px;
  }
  .contact__list {
    list-style: none;
    margin-top: 30px;
    font-size: 16px;
  }
  .contact__list li {
    display: flex; align-items: center;
    height: 21px;
  }
  .contact__list svg {
    width: 14px; height: 14px;
    margin-right: 12px;
    fill: var(--yellow);
    flex: none;
  }
  .contact__address {
    margin-top: 20px;
    font-size: 16px;
    font-style: normal;
    line-height: 20px;
  }

  /* Back */
  .back__brand {
    position: absolute;
    left: 0; top: 0;
    width: 100%; height: 363px;
    display: flex; align-items: center; justify-content: center;
  }
  .back__stripe {
    position: absolute;
    left: 0; top: 363px;
    width: 100%; height: 6px;
    background: var(--yellow);
  }
  .back__footer {
    position: absolute;
    left: 0; top: 382px;
    width: 100%; height: 60px;
    background: var(--black);
    color: var(--muted);
    font-size: 16px;
    display: flex; align-items: center; justify-content: center;
  }
</style>
</head>
<body>

<section class="card card--front">
  <div class="front__brand">
    <p class="brand-name brand-name--front">Vantro<br>Transportation</p>
  </div>
  <div class="front__panel"></div>
  <div class="front__accent"></div>
  <div class="contact">
    <h1 class="contact__name">Daniel Reyes</h1>
    <p class="contact__role">Owner</p>
    <ul class="contact__list">
      <li>
        <svg viewBox="0 0 16 16" aria-hidden="true"><path d="M1 5c0-2 2-3 7-3s7 1 7 3v1h-3V5H4v1H1z"/><path d="M4 7h8l2 6H2z"/></svg>
        (555) 014-2290
      </li>
      <li>
        <svg viewBox="0 0 16 16" aria-hidden="true"><path d="M1 3h14v1L8 9 1 4z"/><path d="M1 6l7 5 7-5v7H1z"/></svg>
        info@vantrotransportation.com
      </li>
      <li>
        <svg viewBox="0 0 16 16" aria-hidden="true"><circle cx="8" cy="8" r="7"/><path d="M5 4c2 1 1 3 3 3s1 3 3 2l1 3c-2 2-6 2-8 0 1-1 1-3 0-4-1-1-1-3 1-4z" fill="#000"/></svg>
        www.vantrotransportation.com
      </li>
    </ul>
    <address class="contact__address">48 Harlow Avenue<br>Brenton, PA 17000</address>
  </div>
</section>

<section class="card card--back">
  <div class="back__brand">
    <p class="brand-name brand-name--back">Vantro<br>Transportation</p>
  </div>
  <div class="back__stripe"></div>
  <div class="back__footer">www.vantrotransportation</div>
</section>

</body>
</html>
```